Business Card Design - ChoiceCraft

Looking for creative, modern design, two sided for ChoiceCraft that is consistent with color and feel of website www.choicecraftpro.net.
Updates

Back of card will be used to promote products or have a quote revolving around decisions, change, leadership, innovation, creativity. Back should also have space to promote website, but optional to use the icon. Front of the card will need to use the icon and have standard place for name, job title, phone and email. We are not looking to put a mailing address or fax. Also want space to place a few words/phrase explaining what we do...such as individual growth and organizational development or tools, training, information...in addition, want the facebook icon small on the front somewhere as we are also on facebook.

Vector file uploaded of icon.

Target Market(s)

Professional coaching for individual growth and organizational development

Industry/Entity Type

Business

Requirements
Must have
• Icon...see attached.

```html
<!DOCTYPE html>
<html lang="en">
<head>
<meta charset="utf-8">
<title>ChoiceCraft Business Card</title>
<link rel="stylesheet" href="https://fonts.googleapis.com/css2?family=Arimo:wght@400;700&family=Tinos:wght@400;700&display=swap">
<style>
  :root {
    --backdrop: #d9dbde;
    --card: #ffffff;
    --brand-blue: #1f8ad0;
    --brand-navy: #2b3a82;
    --text-grey: #444a52;
    --text-dark: #222222;
    --rule-grey: #c4c6c9;
    --mark-blue: #3d9fe0;
    --mark-light: #cfe6f7;
  }
  * { margin: 0; padding: 0; box-sizing: border-box; }
  html, body { width: 1200px; height: 405px; overflow: hidden; }
  body { background: var(--backdrop); position: relative; font-family: "Tinos", serif; }

  .card {
    position: absolute; top: 46px; width: 539px; height: 308px;
    background: var(--card);
    box-shadow: 0 1px 4px rgba(0,0,0,0.25);
  }
  .card--front { left: 41px; }
  .card--back { left: 622px; }

  /* Front */
  .brand { position: absolute; left: 116px; top: 56px; display: flex; align-items: center; gap: 16px; }
  .brand__dot {
    width: 110px; height: 110px; border-radius: 50%;
    background: radial-gradient(circle at 40% 40%, var(--mark-light), var(--mark-blue));
  }
  .brand__name { font-family: "Arimo", sans-serif; font-weight: 700; font-size: 28px; color: var(--brand-blue); }

  .holder { position: absolute; left: 0; right: 0; top: 172px; text-align: center; color: var(--brand-navy); }
  .holder__name { font-weight: 700; font-size: 20px; }
  .holder__title { font-size: 14px; }

  .divider {
    position: absolute; left: 42px; right: 42px; top: 205px; height: 2px;
    background: linear-gradient(90deg, transparent, var(--rule-grey) 20%, var(--rule-grey) 80%, transparent);
  }

  .contact { position: absolute; left: 0; right: 0; top: 214px; text-align: center; color: var(--text-grey); font-size: 13.5px; line-height: 17px; }
  .contact__row { display: flex; justify-content: center; align-items: center; gap: 6px; }
  .contact__item { display: inline-flex; align-items: center; gap: 4px; }
  .contact__icon { width: 11px; height: 11px; }
  .contact__square { width: 9px; height: 9px; background: var(--brand-blue); display: inline-block; }

  .tagline { position: absolute; left: 0; right: 0; top: 258px; text-align: center; color: var(--text-grey); font-size: 14px; line-height: 18px; }

  /* Back */
  .quotes { position: absolute; left: 30px; top: 26px; list-style: none; font-family: "Arimo", sans-serif; }
  .quote { position: relative; height: 53px; padding-left: 30px; }
  .quote__dot {
    position: absolute; left: 0; top: 4px; width: 22px; height: 22px; border-radius: 50%;
    background: radial-gradient(circle at 40% 40%, var(--mark-light), var(--mark-blue));
  }
  .quote__text { font-size: 14px; color: var(--text-dark); line-height: 18px; }
  .quote__mark { font-family: "Tinos", serif; font-weight: 700; font-size: 24px; line-height: 0; color: var(--text-dark); }
  .quote__mark--open { vertical-align: -2px; margin-right: 2px; }
  .quote__mark--close { vertical-align: -10px; margin-left: 1px; }
  .quote__author { font-size: 14px; font-weight: 700; color: var(--brand-blue); padding-left: 14px; margin-top: 1px; }

  .back-dot {
    position: absolute; left: 395px; top: 201px; width: 96px; height: 96px; border-radius: 50%;
    background: radial-gradient(circle at 40% 40%, var(--mark-light), var(--mark-blue));
  }
</style>
</head>
<body>

<section class="card card--front">
  <div class="brand">
    <span class="brand__dot"></span>
    <span class="brand__name">ChoiceCraft</span>
  </div>

  <div class="holder"><span class="holder__name">Your Name,</span> <span class="holder__title">Title</span></div>
  <div class="divider"></div>

  <div class="contact">
    <div class="contact__row">
      <span class="contact__item">
        <svg class="contact__icon" viewBox="0 0 12 12"><path d="M3 1 L5 3.5 L4 5 Q5 7 7 8 L8.5 7 L11 9 L9.5 11 Q5 11 2.5 8 Q0.5 5 1 2.5 Z" fill="none" stroke="#444a52" stroke-width="1"/></svg>
        123-456-789
      </span>
    </div>
    <div class="contact__row">
      <span class="contact__item">
        <svg class="contact__icon" viewBox="0 0 12 12"><rect x="1" y="2.5" width="10" height="7" rx="1" fill="#555"/><path d="M1.5 3 L6 6.5 L10.5 3" fill="none" stroke="#fff" stroke-width="1"/></svg>
        info@choicecraftpro.net
      </span>
      <span class="contact__item">
        <svg class="contact__icon" viewBox="0 0 12 12"><circle cx="6" cy="6" r="5" fill="#555"/><path d="M1 6 H11 M6 1 V11 M6 1 Q3 6 6 11 M6 1 Q9 6 6 11" fill="none" stroke="#fff" stroke-width="0.7"/></svg>
        www.choicecraftpro.net
      </span>
      <span class="contact__item">
        <span class="contact__square"></span>
        /choicecraftpro
      </span>
    </div>
  </div>

  <p class="tagline">Supporting individual growth<br>and organizational development, or tools, training, information</p>
</section>

<section class="card card--back">
  <ul class="quotes">
    <li class="quote">
      <span class="quote__dot"></span>
      <p class="quote__text"><span class="quote__mark quote__mark--open">“</span>Try not to become a man of success, but rather a man of value.<span class="quote__mark quote__mark--close">”</span></p>
      <p class="quote__author">- Arthur Ellison</p>
    </li>
    <li class="quote">
      <span class="quote__dot"></span>
      <p class="quote__text"><span class="quote__mark quote__mark--open">“</span>The only constant is change.<span class="quote__mark quote__mark--close">”</span></p>
      <p class="quote__author">- Helmut Rask</p>
    </li>
    <li class="quote">
      <span class="quote__dot"></span>
      <p class="quote__text"><span class="quote__mark quote__mark--open">“</span>We are what we repeatedly do. Excellence is not an act, it is a habit.<span class="quote__mark quote__mark--close">”</span></p>
      <p class="quote__author">- Ariston Vell</p>
    </li>
    <li class="quote">
      <span class="quote__dot"></span>
      <p class="quote__text"><span class="quote__mark quote__mark--open">“</span>Simplicity is the ultimate sophistication.<span class="quote__mark quote__mark--close">”</span></p>
      <p class="quote__author">- Leonard Davies</p>
    </li>
    <li class="quote">
      <span class="quote__dot"></span>
      <p class="quote__text"><span class="quote__mark quote__mark--open">“</span>Life is not fair - get used to it.<span class="quote__mark quote__mark--close">”</span></p>
      <p class="quote__author">- Bill Garner</p>
    </li>
  </ul>
  <span class="back-dot"></span>
</section>

</body>
</html>
```